delivery service for warm food for kids and other kids stuff

plumhaven.nl > daycare website

plumhaven.shop >>> shopify site we ask you to design!

We are a daycare center and thanks to corona found that we could help parents and kids while at home ! we would like some help to get an awesome and clear site for this.

it doesnt have to look kiddy...
more proffessional and sleek
we love quillon website... so anything in that direction would be great!... ie pic next to text...
2 tone colors
ours are pink light blue and white.. so play with that?
black and white also fine!

Target Market(s)

expats and proffesional parents ... so NOT KIDDY website...

Font styles to use
Sans Serif

Requirements
Must have
• sexy design....
simplicity...
less text... more pictures
cool headlines
Should not have
• lots of text everyhwere
busy

```html
<!DOCTYPE html>
<html lang="en">
<head>
<meta charset="utf-8">
<title>Plumhaven Shop</title>
<link href="https://fonts.googleapis.com/css2?family=Lato:wght@400;700;900&family=Open+Sans:wght@700;800&display=swap" rel="stylesheet">
<style>
:root{
  --pink:#e8507f;
  --blue-top:#6cc0ee;
  --blue-bottom:#1e88e5;
  --cyan:#12b5ea;
  --ink:#333;
  --body:#444;
  --line:#e3e3e3;
  --bar:#f6f6f6;
  --white:#fff;
  --social:#2b2b2b;
}
*{box-sizing:border-box;margin:0;padding:0}
html,body{width:1200px;height:2712px;overflow:hidden;background:var(--white)}
body{position:relative;font-family:'Lato',sans-serif;color:var(--ink)}

/* header */
.site-header{position:absolute;left:0;top:0;width:1200px;height:75px;background:var(--bar);border-bottom:1px solid var(--line)}
.brand{position:absolute;display:flex;align-items:center;gap:6px;font-weight:900;color:var(--pink)}
.brand-dot{width:18px;height:18px;border-radius:50%;background:var(--cyan)}
.site-header .brand{left:100px;top:27px;font-size:17px}
.search{position:absolute;left:286px;top:25px;width:244px;height:24px;background:var(--white);border:1px solid var(--line);font-size:8px;color:#888;padding:7px 6px}
.search-btn{position:absolute;right:-1px;top:-1px;width:30px;height:24px;background:var(--cyan);border-radius:0 3px 3px 0}
.nav a{position:absolute;top:30px;font-size:10px;color:#555;text-decoration:none}
.nav .active-bar{position:absolute;left:645px;top:0;width:38px;height:2px;background:var(--cyan)}
.login{position:absolute;left:1016px;top:27px;width:50px;height:20px;border:1px solid var(--pink);border-radius:3px;color:var(--pink);font-size:10px;text-align:center;line-height:18px}
.cart{position:absolute;left:1073px;top:24px;width:27px;height:27px;border-radius:50%;background:var(--pink)}

/* hero */
.hero{position:absolute;left:0;top:75px;width:1200px;height:625px;
  background:
    radial-gradient(ellipse 210px 190px at 590px 330px,rgba(230,150,70,.95),rgba(230,150,70,0) 100%),
    radial-gradient(ellipse 250px 120px at 600px 520px,rgba(215,90,45,.8),rgba(215,90,45,0)),
    radial-gradient(ellipse 300px 200px at 330px 30px,rgba(240,236,226,.95),rgba(240,236,226,0)),
    radial-gradient(ellipse 270px 160px at 900px 20px,rgba(238,238,232,.95),rgba(238,238,232,0)),
    radial-gradient(ellipse 270px 220px at 200px 600px,rgba(236,228,216,.9),rgba(236,228,216,0)),
    radial-gradient(ellipse 300px 190px at 1070px 600px,rgba(232,232,226,.9),rgba(232,232,226,0)),
    radial-gradient(ellipse 140px 170px at 1080px 260px,rgba(230,120,60,.75),rgba(230,120,60,0)),
    radial-gradient(ellipse 130px 150px at 120px 270px,rgba(150,80,50,.8),rgba(150,80,50,0)),
    linear-gradient(160deg,#5a3022,#7b3d26 40%,#6a3321 70%,#4c271b)}
.hero-title{position:absolute;left:0;width:1200px;top:266px;text-align:center;font-family:'Open Sans',sans-serif;font-weight:800;font-size:74px;color:var(--white);text-shadow:0 3px 8px rgba(0,0,0,.5)}
.hero-sub{position:absolute;left:0;width:1200px;top:366px;text-align:center;font-family:'Open Sans',sans-serif;font-weight:700;font-size:37px;color:var(--white);text-shadow:0 3px 8px rgba(0,0,0,.5)}
.btn{position:absolute;display:flex;align-items:center;justify-content:center;font-weight:900;color:var(--white);border-radius:4px;box-shadow:0 3px 6px rgba(0,0,0,.18);font-size:14px;letter-spacing:.3px}
.btn-pink{background:var(--pink)}
.btn-cyan{background:var(--cyan)}

/* featured */
.section-title{position:absolute;font-weight:700;font-size:32px;color:var(--ink)}
.card{position:absolute;top:838px;width:234px;height:287px;background:var(--white);box-shadow:0 1px 5px rgba(0,0,0,.2);border-radius:3px;overflow:hidden}
.card-img{height:237px}
.card-name{position:absolute;left:12px;top:247px;font-size:12px;color:var(--ink)}
.card-price{position:absolute;left:12px;top:266px;font-size:10px;color:#999}
.page{position:absolute;top:1151px;width:18px;height:20px;border-radius:2px;background:#ddd;color:var(--white);font-size:9px;text-align:center;line-height:20px}
.page.current{background:var(--cyan)}

/* blue band */
.band{position:absolute;left:0;top:1230px;width:1200px;height:449px;background:linear-gradient(180deg,var(--blue-top),var(--blue-bottom))}
.band h2{position:absolute;left:101px;top:94px;font-size:32px;line-height:38px;color:var(--white);font-weight:700}
.band p{position:absolute;left:101px;top:189px;width:470px;font-size:11px;line-height:16px;color:var(--white)}
.read-more{position:absolute;left:101px;top:255px;font-size:8px;font-weight:700;color:#7ef05a}
.feature{position:absolute;top:330px;width:80px;text-align:center;color:var(--white);font-size:8px;font-weight:700}
.feature svg{display:block;margin:0 auto 4px}
.band-img{position:absolute;left:639px;top:44px;width:461px;height:367px;border-radius:6px;
  background:
    radial-gradient(ellipse 120px 150px at 160px 180px,rgba(120,140,190,.8),rgba(120,140,190,0)),
    radial-gradient(ellipse 90px 120px at 230px 210px,rgba(210,120,150,.55),rgba(210,120,150,0)),
    radial-gradient(ellipse 110px 140px at 350px 210px,rgba(200,120,120,.55),rgba(200,120,120,0)),
    linear-gradient(180deg,rgba(0,0,0,0) 65%,rgba(60,80,110,.55) 80%,rgba(90,110,140,.4)),
    linear-gradient(90deg,#dfe7f2,#b9c9de 30%,#9fb3cf 60%,#c7d4e4)}

/* split blocks */
.photo{position:absolute;border-radius:6px}
.copy{position:absolute;font-size:12.5px;line-height:19px;color:var(--body)}
.copy p{margin-bottom:18px}

/* footer */
.footer-rule{position:absolute;left:100px;top:2554px;width:1000px;height:1px;background:var(--line)}
.fcol{position:absolute;top:2567px;font-size:9.5px;line-height:16px;color:#666}
.fcol h4{font-size:9.5px;font-weight:700;color:#555;margin-bottom:5px}
.social{display:flex;align-items:center;gap:8px;font-size:8px;height:29px}
.social i{width:20px;height:20px;border-radius:50%;background:var(--social);display:block}
.copyright{position:absolute;left:0;width:1200px;top:2682px;text-align:center;font-size:7px;color:#666}
</style>
</head>
<body>

<header class="site-header">
  <div class="brand"><span class="brand-dot"></span>Plumhaven</div>
  <div class="search">Search here . . .
    <span class="search-btn">
      <svg width="30" height="24" viewBox="0 0 30 24"><circle cx="14" cy="11" r="5" fill="none" stroke="#fff" stroke-width="1.5"/><line x1="18" y1="15" x2="21" y2="18" stroke="#fff" stroke-width="1.5"/></svg>
    </span>
  </div>
  <nav class="nav">
    <span class="active-bar"></span>
    <a style="left:650px">Home</a>
    <a style="left:731px">Delivery</a>
    <a style="left:824px">Our Products</a>
    <a style="left:941px">Blog</a>
  </nav>
  <div class="login">Login</div>
  <div class="cart">
    <svg width="27" height="27" viewBox="0 0 27 27"><path d="M8 9h2l2 7h7l1.5-5H11" fill="none" stroke="#fff" stroke-width="1.3"/><circle cx="13" cy="18.5" r="1" fill="#fff"/><circle cx="18" cy="18.5" r="1" fill="#fff"/></svg>
  </div>
</header>

<section class="hero" role="img" aria-label="Overhead photo of plates of colourful vegetables, dishes and drinks on a wooden table"></section>
<h1 class="hero-title">Plumhaven Shop</h1>
<div class="hero-sub">Curated for you by Plumhaven Kids!</div>
<div class="btn btn-pink" style="left:468px;top:433px;width:252px;height:48px">MAKE ORDER NOW</div>

<h2 class="section-title" style="left:0;width:1200px;top:745px;text-align:center">Featured&nbsp; Colection</h2>

<article class="card" style="left:100px">
  <div class="card-img" role="img" aria-label="Pasta with tomato sauce and basil" style="background:radial-gradient(ellipse 70px 60px at 190px 50px,rgba(70,140,60,.85),rgba(70,140,60,0)),radial-gradient(ellipse 150px 110px at 110px 140px,#f7a93c,rgba(247,169,60,0)),linear-gradient(160deg,#f4b050,#e0691f 55%,#c9452a 80%,#e8e2da)"></div>
  <div class="card-name">Pasta Bolognese 1-2 year olds</div>
  <div class="card-price">€4,00</div>
</article>
<article class="card" style="left:356px">
  <div class="card-img" role="img" aria-label="Plate of rice stew with chicken on a wooden table" style="background:radial-gradient(ellipse 80px 60px at 120px 125px,#f1ece0,#dfd4bf 60%,rgba(223,212,191,0) 100%),radial-gradient(ellipse 110px 90px at 120px 135px,#f6f4ef 70%,rgba(246,244,239,0)),linear-gradient(160deg,#7a4a32,#5a3826 50%,#3f2a1e)"></div>
  <div class="card-name">Pea stew with chicken t 1-2 year olds</div>
  <div class="card-price">€4,00</div>
</article>
<article class="card" style="left:611px">
  <div class="card-img" role="img" aria-label="Jars of colourful fruit smoothies" style="background:linear-gradient(180deg,rgba(60,40,28,.9) 0%,rgba(60,40,28,.7) 38%,rgba(0,0,0,0) 45%,rgba(0,0,0,0) 88%,rgba(50,50,40,.6)),linear-gradient(90deg,#8fb060 0 24%,#5a3a2a 24% 26%,#7b4b95 26% 50%,#5a3a2a 50% 52%,#efc95a 52% 76%,#5a3a2a 76% 78%,#ea97ad 78%)"></div>
  <div class="card-name">Smoothie</div>
  <div class="card-price">€3,25</div>
</article>
<article class="card" style="left:866px">
  <div class="card-img" role="img" aria-label="Two bottles of water" style="background:radial-gradient(ellipse 40px 100px at 85px 150px,rgba(255,255,255,.85),rgba(255,255,255,0)),radial-gradient(ellipse 40px 90px at 150px 160px,rgba(255,255,255,.8),rgba(255,255,255,0)),linear-gradient(180deg,#dfe5ee,#c3cddb 70%,#d6dde7)"></div>
  <div class="card-name">Pasta Bolognese 1-2 year olds</div>
  <div class="card-price">€2,00</div>
</article>

<div class="page current" style="left:566px">1</div>
<div class="page" style="left:591px">2</div>
<div class="page" style="left:616px">3</div>

<section class="band">
  <h2>We Deliver High Quality Food<br>For Kids</h2>
  <p>Lorem ipsum dolor sit amet, consectetur adipiscing elit, sed do eiusmod tempor incididunt ut labore et dolore magna aliqua. Quis ipsum suspendisse ultrices gravida. Risus commodo viverra maecenas accumsan lacus vel facilisis. Lorem ipsum dolor sit amet, consectetur adipiscing elit, sed do eiusmod tempor incididunt</p>
  <div class="read-more">READ MORE</div>
  <div class="feature" style="left:93px">
    <svg width="62" height="54" viewBox="0 0 62 54" fill="none" stroke="#fff" stroke-width="2"><rect x="4" y="4" width="22" height="16"/><line x1="8" y1="10" x2="22" y2="10"/><line x1="8" y1="15" x2="18" y2="15"/><path d="M14 40h30l6-14h-10"/><circle cx="14" cy="44" r="6"/><circle cx="50" cy="44" r="6"/><path d="M30 20h10v20"/></svg>
    FAST DELIVERY
  </div>
  <div class="feature" style="left:227px">
    <svg width="54" height="54" viewBox="0 0 54 54" fill="none" stroke="#fff" stroke-width="2"><path d="M27 3l6 5 8-1 2 8 7 4-3 7 3 7-7 4-2 8-8-1-6 5-6-5-8 1-2-8-7-4 3-7-3-7 7-4 2-8 8 1z"/><line x1="19" y1="35" x2="35" y2="19"/><circle cx="20" cy="20" r="3"/><circle cx="34" cy="34" r="3"/></svg>
    CHEAP
  </div>
  <div class="feature" style="left:358px">
    <svg width="50" height="54" viewBox="0 0 50 54" fill="none" stroke="#fff" stroke-width="2"><circle cx="25" cy="19" r="16"/><circle cx="25" cy="19" r="10"/><path d="M14 32l-5 16 7-3 4 6 5-14"/><path d="M36 32l5 16-7-3-4 6-5-14"/></svg>
    BEST QUALITY
  </div>
  <div class="band-img" role="img" aria-label="Family sharing a meal at a glass dining table"></div>
</section>

<div class="photo" role="img" aria-label="Family sitting together outdoors among trees, seen from behind" style="left:99px;top:1742px;width:504px;height:378px;background:radial-gradient(ellipse 110px 170px at 110px 250px,rgba(110,130,160,.9),rgba(110,130,160,0)),radial-gradient(ellipse 140px 190px at 420px 260px,rgba(130,150,175,.9),rgba(130,150,175,0)),radial-gradient(ellipse 90px 110px at 290px 260px,rgba(175,185,200,.8),rgba(175,185,200,0)),radial-gradient(ellipse 160px 120px at 260px 60px,rgba(220,230,190,.9),rgba(220,230,190,0)),linear-gradient(180deg,#b9c78e,#7f924f 45%,#55663a)"></div>
<h2 class="section-title" style="left:654px;top:1734px">We Care For Our Clients</h2>
<div class="copy" style="left:654px;top:1797px;width:400px">
  <p>Lorem ipsum dolor sit amet, consectetur adipiscing elit, sed do eiusmod tempor incididunt ut labore et dolore magna aliqua. Quis ipsum suspendisse ultrices gravida.</p>
  <p>Lorem ipsum dolor sit amet, consectetur adipiscing elit, sed do eiusmod tempor incididunt ut labore et dolore magna aliqua. Quis ipsum suspendisse ultrices gravida.</p>
  <p>Lorem ipsum dolor sit amet, consectetur adipiscing elit, sed do eiusmod tempor incididunt ut labore et dolore magna aliqua. Quis ipsum suspendisse ultrices gravida.</p>
</div>
<div class="btn btn-cyan" style="left:653px;top:2013px;width:252px;height:49px">FIND OUT MORE ABOUT US</div>

<h2 class="section-title" style="left:100px;top:2163px">Warm &amp; Tasty Food</h2>
<div class="copy" style="left:100px;top:2226px;width:400px">
  <p>Lorem ipsum dolor sit amet, consectetur adipiscing elit, sed do eiusmod tempor incididunt ut labore et dolore magna aliqua. Quis ipsum suspendisse ultrices gravida.</p>
  <p>Lorem ipsum dolor sit amet, consectetur adipiscing elit, sed do eiusmod tempor incididunt ut labore et dolore magna aliqua. Quis ipsum suspendisse ultrices gravida.</p>
  <p>Lorem ipsum dolor sit amet, consectetur adipiscing elit, sed do eiusmod tempor incididunt ut labore et dolore magna aliqua. Quis ipsum suspendisse ultrices gravida.</p>
</div>
<div class="btn btn-pink" style="left:101px;top:2442px;width:251px;height:49px">ORDER NOW</div>
<div class="photo" role="img" aria-label="Overhead view of friends sharing pizza and takeaway dishes on a wooden table" style="left:598px;top:2112px;width:502px;height:377px;background:radial-gradient(ellipse 70px 60px at 230px 150px,rgba(200,80,50,.8),rgba(200,80,50,0)),radial-gradient(ellipse 70px 60px at 300px 220px,rgba(205,120,60,.8),rgba(205,120,60,0)),radial-gradient(ellipse 60px 50px at 120px 230px,rgba(225,215,195,.8),rgba(225,215,195,0)),radial-gradient(ellipse 60px 50px at 400px 170px,rgba(225,210,185,.8),rgba(225,210,185,0)),radial-gradient(ellipse 220px 120px at 250px 200px,#a8927a,rgba(168,146,122,0)),linear-gradient(180deg,#3a3b42,#55504d 25%,#7c6f63 50%,#55504d 75%,#34353c)"></div>

<footer>
  <div class="footer-rule"></div>
  <div class="fcol" style="left:100px">
    <h4>Quick Links</h4>
    Home<br>Delivery<br>Our Products<br>Blog
  </div>
  <div class="fcol" style="left:344px">
    <h4>Partners</h4>
    Lorem<br>Ipsum<br>Ipsum<br>Lorem
  </div>
  <div class="brand" style="left:562px;top:2582px;font-size:14px"><span class="brand-dot"></span>Plumhaven</div>
  <div class="fcol" style="left:765px">
    <h4>Contact Us</h4>
    Plumhaven Shop LLC<br>d.b.a PlumhavenShop<br>250 Harbor Lane<br>Suite 40<br>Dover, DE 19901
  </div>
  <div class="fcol" style="left:992px">
    <h4>Keep Conected</h4>
    <div class="social"><i></i>Follow us on Chirper</div>
    <div class="social"><i></i>Follow us on Linkwork</div>
    <div class="social"><i></i>Like us on Facepage</div>
    <div class="social"><i></i>Subscribe to our feed</div>
  </div>
  <div class="copyright">© 2020, PlumhavenKids All Rights Reserved.</div>
</footer>

</body>
</html>
```